Business Card for Coastal Tundrabridge Advisory

We need a business card for Coastal Tundrabridge Advisory. The company website address is provided below. The company logo is attached. We provide specialized permafrost services to the mining, transportation, and oil & gas industries. The card should be prepared for:
Matthias Korhonen, PhD.
Coastal Tundrabridge Advisory
PO Box 418259
Quillwater, Alaska 99642
Direct: +1-907-555-0143
Email: mkorhonen@tundrabridgeadvisory.example
Website: www.coastaltundrabridgeadvisory.example

```html
<!DOCTYPE html>
<html lang="en">
<head>
<meta charset="utf-8">
<title>Coastal Tundrabridge Advisory – Business Card</title>
<link rel="stylesheet" href="https://fonts.googleapis.com/css2?family=Montserrat:wght@400;500;700&display=swap">
<style>
  :root {
    --ink: #111822;
    --ink-soft: #1c2430;
    --paper: #ffffff;
    --stage: #e9e7e3;
    --text: #1a1f27;
  }
  * { margin: 0; padding: 0; box-sizing: border-box; }
  html, body { width: 1200px; height: 931px; overflow: hidden; }
  body {
    background: var(--stage);
    font-family: "Montserrat", sans-serif;
    color: var(--text);
    display: flex;
    flex-direction: column;
    align-items: center;
    justify-content: center;
    gap: 44px;
  }
  .card {
    width: 700px;
    height: 400px;
    border-radius: 22px;
    overflow: hidden;
    position: relative;
    box-shadow: 0 8px 24px rgba(0,0,0,0.18);
  }

  /* Back side */
  .card-back { background: var(--ink); }
  .back-texture {
    position: absolute; inset: 0;
    background: linear-gradient(125deg, #3a414b 0%, #1a212b 35%, #10161f 70%, #141b25 100%);
  }
  .back-name {
    position: absolute;
    right: 70px; bottom: 80px;
    color: var(--paper);
    font-weight: 700;
    font-size: 22px;
    letter-spacing: 0.12em;
    text-transform: uppercase;
    line-height: 1.3;
    text-align: right;
  }

  /* Front side */
  .card-front { background: var(--paper); display: flex; }
  .front-info {
    width: 445px;
    padding: 58px 0 0 50px;
    position: relative;
  }
  .person-name { font-weight: 700; font-size: 27px; color: var(--ink); }
  .person-title { font-weight: 400; font-size: 16px; margin-top: 2px; }
  .address {
    position: absolute; left: 50px; top: 210px;
    font-size: 16px; line-height: 1.3;
  }
  .contacts {
    position: absolute; left: 50px; top: 275px;
    list-style: none;
    font-size: 15.5px;
  }
  .contacts li { display: flex; align-items: center; gap: 12px; height: 30px; }
  .contacts svg { width: 16px; height: 16px; flex: none; fill: var(--ink); }
  .front-brand {
    flex: 1;
    background: var(--ink);
    display: flex;
    align-items: center;
    justify-content: center;
  }
  .brand-name {
    color: var(--paper);
    font-weight: 700;
    font-size: 20px;
    letter-spacing: 0.12em;
    text-transform: uppercase;
    line-height: 1.35;
    text-align: center;
  }
</style>
</head>
<body>

  <section class="card card-back">
    <div class="back-texture" role="img" aria-label="Faint repeated company name pattern on dark background"></div>
    <p class="back-name">Coastal<br>Tundrabridge<br>Advisory</p>
  </section>

  <section class="card card-front">
    <div class="front-info">
      <h1 class="person-name">Matthias Korhonen, PhD.</h1>
      <p class="person-title">Managing Director</p>

      <p class="address">PO Box 418259<br>Quillwater, Alaska 99642</p>

      <ul class="contacts">
        <li>
          <svg viewBox="0 0 16 16" aria-hidden="true"><path d="M3.6 1.2l2.3 2.6-1.4 1.8c.9 2 2.4 3.5 4.4 4.4l1.8-1.4 2.6 2.3-1.4 2.5C6.8 13.6 2.4 9.2 1.1 2.6z"/></svg>
          <span>+1-907-555-0143</span>
        </li>
        <li>
          <svg viewBox="0 0 16 16" aria-hidden="true"><path d="M1 3h14v1.2L8 9 1 4.2z"/><path d="M1 5.6l7 4.8 7-4.8V13H1z"/></svg>
          <span>mkorhonen@tundrabridgeadvisory.example</span>
        </li>
        <li>
          <svg viewBox="0 0 16 16" aria-hidden="true"><circle cx="8" cy="8" r="7"/><path d="M1 8h14M8 1c2.5 2.5 2.5 11.5 0 14M8 1C5.5 3.5 5.5 12.5 8 15" stroke="#fff" stroke-width="1" fill="none"/></svg>
          <span>www.coastaltundrabridgeadvisory.example</span>
        </li>
      </ul>
    </div>
    <div class="front-brand">
      <p class="brand-name">Coastal<br>Tundrabridge<br>Advisory</p>
    </div>
  </section>

</body>
</html>
```